Business Card for Coastal Tundrabridge Advisory

We need a business card for Coastal Tundrabridge Advisory. The company website address is provided below. The company logo is attached. We provide specialized permafrost services to the mining, transportation, and oil & gas industries. The card should be prepared for:
Matthias Korhonen, PhD.
Coastal Tundrabridge Advisory
PO Box 418259
Quillwater, Alaska 99642
Direct: +1-907-555-0143
Email: mkorhonen@tundrabridgeadvisory.example
Website: www.coastaltundrabridgeadvisory.example

```html
<!DOCTYPE html>
<html lang="en">
<head>
<meta charset="utf-8">
<title>Coastal Tundrabridge Advisory – Business Card</title>
<link rel="stylesheet" href="https://fonts.googleapis.com/css2?family=Jost:wght@400;500&display=swap">
<style>
  :root {
    --backdrop: #d9dadc;
    --card: #ffffff;
    --ink: #1b2029;
    --muted: #6d7078;
    --band: #151b24;
  }
  * { box-sizing: border-box; margin: 0; padding: 0; }
  html, body { width: 1200px; height: 900px; overflow: hidden; }
  body {
    background: var(--backdrop);
    font-family: "Jost", "Helvetica Neue", Arial, sans-serif;
    color: var(--ink);
    position: relative;
  }
  .card {
    position: absolute;
    width: 580px;
    height: 330px;
    background: var(--card);
    box-shadow: 0 10px 28px rgba(0,0,0,0.18);
    overflow: hidden;
  }
  .card::after {
    content: "";
    position: absolute;
    left: 0; right: 0; bottom: 0;
    height: 16px;
    background: var(--band);
  }
  .card--front { left: 80px; top: 80px; }
  .card--back  { left: 540px; top: 490px; }

  .wordmark {
    position: absolute;
    left: 0; right: 0;
    text-align: center;
    font-weight: 500;
    text-transform: uppercase;
    letter-spacing: 0.16em;
    color: var(--ink);
    white-space: nowrap;
  }
  .card--front .wordmark { top: 145px; font-size: 22px; }
  .card--back  .wordmark { top: 58px;  font-size: 19px; }

  .holder {
    position: absolute;
    left: 36px;
    top: 168px;
  }
  .holder__name {
    font-size: 17px;
    font-weight: 500;
    text-transform: uppercase;
    letter-spacing: 0.01em;
  }
  .holder__company {
    font-size: 14px;
    color: var(--muted);
    margin-top: 1px;
  }
  .contacts {
    list-style: none;
    margin-top: 18px;
  }
  .contacts li {
    display: flex;
    align-items: center;
    gap: 9px;
    font-size: 13px;
    color: var(--muted);
    line-height: 22px;
    white-space: nowrap;
  }
  .contacts svg { width: 13px; height: 13px; flex: none; }

  .address {
    position: absolute;
    left: 368px;
    top: 230px;
    padding-left: 12px;
    border-left: 1.5px solid var(--ink);
    font-size: 13px;
    line-height: 19px;
    color: var(--muted);
    white-space: nowrap;
  }
</style>
</head>
<body>

  <section class="card card--front" aria-label="Card front">
    <div class="wordmark">Coastal Tundrabridge Advisory</div>
  </section>

  <section class="card card--back" aria-label="Card back">
    <div class="wordmark">Coastal Tundrabridge Advisory</div>

    <div class="holder">
      <p class="holder__name">Matthias Korhonen, PhD.</p>
      <p class="holder__company">Coastal Tundrabridge Advisory</p>
      <ul class="contacts">
        <li>
          <svg viewBox="0 0 16 16" aria-hidden="true"><path fill="#1b2029" d="M3.6 1.5l2.2 2.6-1.2 1.7c.9 2 2.5 3.6 4.5 4.5l1.7-1.2 2.6 2.2-1 2.3C7.3 13.3 2.7 8.7 1.4 3.6z"/></svg>
          +1-907-555-0143
        </li>
        <li>
          <svg viewBox="0 0 16 16" aria-hidden="true"><rect x="1" y="3" width="14" height="10" fill="#1b2029"/><path d="M1.5 3.5L8 9l6.5-5.5" fill="none" stroke="#fff" stroke-width="1.3"/></svg>
          mkorhonen@tundrabridgeadvisory.example
        </li>
        <li>
          <svg viewBox="0 0 16 16" aria-hidden="true" fill="none" stroke="#1b2029" stroke-width="1.1"><circle cx="8" cy="8" r="6.5"/><ellipse cx="8" cy="8" rx="2.8" ry="6.5"/><path d="M1.5 8h13M2.6 4.6h10.8M2.6 11.4h10.8"/></svg>
          www.coastaltundrabridgeadvisory.example
        </li>
      </ul>
    </div>

    <address class="address" style="font-style: normal;">
      PO Box 418259<br>
      Quillwater, Alaska 99642
    </address>
  </section>

</body>
</html>
```